Modern Attractive Letterhead for Veterinary House Call Business.

A letterhead which can be printed on A4, A5 and A6 paper sizes.
To have: ( our files to be uploaded)
1. Logo with Text
2. telephone
3. email
4. website
5. Address

Target Market(s)

60-85year mainly women pet owners. Also market include families, young professionals, busy people who have dogs and cats

Industry/Entity Type

Business

Requirements
Must have
• 1. Logo with Text ( provided)
• 2. telephone
• 3. email
• 4. website
• 5. Address
Nice to have
• Needs to be modern, preferably warm and caring in nature( if possible )
Should not have
• difficulty in printing A5 and A6

```html
<!DOCTYPE html>
<html lang="en">
<head>
<meta charset="utf-8">
<title>Hearthside Vet Care – Letterhead</title>
<link href="https://fonts.googleapis.com/css2?family=Cinzel:wght@400;600&display=swap" rel="stylesheet">
<style>
  :root {
    --paper: #ffffff;
    --page-bg: #f4f4f4;
    --brand-blue: #2c6fb5;
    --brand-green: #3f9a35;
    --ink: #2b2b3a;
    --wash-blue: #dfe6ef;
    --wash-green: #e6efe4;
  }
  html, body {
    margin: 0;
    padding: 0;
    width: 960px;
    height: 1200px;
    overflow: hidden;
    background: var(--page-bg);
  }
  .letterhead {
    position: relative;
    width: 960px;
    height: 1200px;
    background: linear-gradient(160deg, var(--paper) 35%, #f3f4f6 100%);
    font-family: "Cinzel", serif;
    color: var(--ink);
    overflow: hidden;
  }
  .brand {
    position: absolute;
    top: 52px;
    left: 0;
    width: 100%;
    display: flex;
    justify-content: center;
    align-items: center;
    gap: 18px;
  }
  .brand-dot {
    width: 44px;
    height: 44px;
    border-radius: 50%;
    background: var(--brand-blue);
  }
  .brand-name {
    font-family: "Cinzel", serif;
    font-weight: 600;
    font-size: 44px;
    letter-spacing: 1px;
    color: var(--brand-blue);
    margin: 0;
  }
  .footer-wash {
    position: absolute;
    left: 0;
    bottom: 0;
    width: 100%;
    height: 520px;
    background: radial-gradient(ellipse at 62% 100%, var(--wash-blue) 0%, rgba(223,230,239,0.5) 35%, rgba(255,255,255,0) 70%),
                linear-gradient(to top, var(--wash-green) 0%, rgba(230,239,228,0) 45%);
    opacity: 0.8;
  }
  .contact {
    position: absolute;
    left: 0;
    bottom: 14px;
    width: 100%;
    text-align: center;
  }
  .contact-address {
    font-size: 18px;
    letter-spacing: 0.5px;
    margin: 0 0 8px;
  }
  .contact-lines {
    display: flex;
    justify-content: center;
    align-items: center;
    gap: 22px;
    font-size: 15px;
    letter-spacing: 0.3px;
    margin: 0;
  }
  .contact-item {
    display: inline-flex;
    align-items: center;
    gap: 7px;
  }
  .contact-icon {
    width: 13px;
    height: 13px;
    fill: none;
    stroke: var(--brand-green);
    stroke-width: 1.6;
  }
</style>
</head>
<body>
  <main class="letterhead">
    <header class="brand">
      <span class="brand-dot"></span>
      <h1 class="brand-name">Hearthside Vet Care</h1>
    </header>

    <div class="footer-wash" role="img" aria-label="Soft decorative colour wash at the foot of the page"></div>

    <footer class="contact">
      <p class="contact-address">PO Box 4821 Brookfield Ridge QLD 4070</p>
      <p class="contact-lines">
        <span class="contact-item">
          <svg class="contact-icon" viewBox="0 0 14 14" aria-hidden="true"><path d="M3 1.5 L5 1.5 L6 4.5 L4.5 5.8 Q6 8.3 8.2 9.5 L9.5 8 L12.5 9 L12.5 11 Q12 12.5 10.5 12.5 Q2 11.5 1.5 3.5 Q1.5 2 3 1.5 Z"/></svg>
          0400123456
        </span>
        <span class="contact-item">
          <svg class="contact-icon" viewBox="0 0 14 14" aria-hidden="true"><rect x="1" y="3" width="12" height="8.5" rx="1"/><path d="M1 3.5 L7 8 L13 3.5"/></svg>
          hello@hearthsidevet.com.au
        </span>
        <span class="contact-item">
          <svg class="contact-icon" viewBox="0 0 14 14" aria-hidden="true"><circle cx="7" cy="7" r="5.8"/><ellipse cx="7" cy="7" rx="2.6" ry="5.8"/><path d="M1.2 7 H12.8"/></svg>
          www.hearthsidevet.com.au
        </span>
      </p>
    </footer>
  </main>
</body>
</html>
```